Card Design for my dog training business Brightpaw Obedience

Need a business card design for my dog training business with my new logo. Want the card to come off professional yet fun. Want it to be very eye catchy as well. I normally have these at vet clinics, pet stores, and groomers. so need it to look better than my competitors.
Target Market(s)
dog owners
Industry/Entity Type
Dog Training
Contact Information for Business Card
needs logo, my name and info
Font styles to use
Serif
Colors
0255a3
ffffff
ec1f27
000000
333333
fbfbfb
Requirements
Must have
- Brightpaw Obedience
- Felix Orland
- 415 903 2276
- info@brightpawobedience.example
- www.brightpawobedience.example

```html
<!DOCTYPE html>
<html lang="en">
<head>
<meta charset="utf-8">
<title>Brightpaw Obedience — Business Card</title>
<link href="https://fonts.googleapis.com/css2?family=Tinos&family=Lato:wght@400&display=swap" rel="stylesheet">
<style>
  :root {
    --blue: #0255a3;
    --white: #ffffff;
    --black: #000000;
    --panel: #1e1e1f;
    --ink: #333333;
    --paper: #fbfbfb;
    --backdrop: #e4e4e4;
  }
  * { margin: 0; padding: 0; box-sizing: border-box; }
  html, body {
    width: 1200px;
    height: 900px;
    overflow: hidden;
    background: var(--backdrop);
  }
  .card {
    position: absolute;
    left: 150px;
    top: 171px;
    width: 900px;
    height: 558px;
    background: var(--paper);
    overflow: hidden;
    box-shadow: 0 10px 30px rgba(0,0,0,0.18);
  }
  .brand {
    position: absolute;
    left: 24px;
    top: 224px;
    width: 360px;
    display: flex;
    align-items: center;
    justify-content: center;
    gap: 16px;
    font-family: "Tinos", "Times New Roman", serif;
    font-size: 46px;
    line-height: 1.1;
    color: var(--black);
    text-align: center;
  }
  .brand-mark {
    width: 22px;
    height: 22px;
    border-radius: 50%;
    background: var(--blue);
    flex: none;
  }
  .panel {
    position: absolute;
    left: 0;
    top: 0;
    width: 900px;
    height: 558px;
  }
  .holder-name {
    position: absolute;
    right: 65px;
    top: 178px;
    font-family: "Tinos", "Times New Roman", serif;
    font-size: 33px;
    color: var(--blue);
    letter-spacing: 0.5px;
    text-transform: uppercase;
  }
  .contact {
    position: absolute;
    right: 62px;
    top: 378px;
    list-style: none;
    font-family: "Lato", "Helvetica", sans-serif;
    font-size: 23px;
    color: var(--white);
  }
  .contact li {
    display: flex;
    justify-content: flex-end;
    align-items: center;
    gap: 8px;
    height: 33px;
  }
  .contact svg { width: 19px; height: 19px; flex: none; }
</style>
</head>
<body>
  <div class="card">
    <div class="brand"><span class="brand-mark"></span><span>Brightpaw<br>Obedience</span></div>

    <svg class="panel" viewBox="0 0 900 558" role="img" aria-label="Dark panel with a curved blue-edged border where a dog silhouette belongs">
      <path d="M505 0 C430 110 385 290 400 390 C412 470 465 520 482 558 L900 558 L900 0 Z" fill="#0255a3"/>
      <path d="M512 0 C438 110 393 290 408 390 C420 470 472 520 490 558 L900 558 L900 0 Z" fill="#1e1e1f"/>
    </svg>

    <div class="holder-name">Felix Orland</div>

    <ul class="contact">
      <li>415 903 2276
        <svg viewBox="0 0 20 20" aria-hidden="true"><path fill="#0255a3" d="M2 7c0-3 3-4 8-4s8 1 8 4v1h-4V6.5c0-.6-1.5-1-4-1s-4 .4-4 1V8H2z M5 10l2-3h6l2 3v6H5z"/><circle cx="10" cy="12.5" r="1.8" fill="#1e1e1f"/></svg>
      </li>
      <li>info@brightpawobedience.example
        <svg viewBox="0 0 20 20" aria-hidden="true"><rect x="2" y="4" width="16" height="12" rx="1" fill="#0255a3"/><path d="M2.5 4.5 10 11l7.5-6.5" fill="none" stroke="#1e1e1f" stroke-width="1.4"/></svg>
      </li>
      <li>www.brightpawobedience.example
        <svg viewBox="0 0 20 20" aria-hidden="true"><circle cx="10" cy="10" r="8" fill="#0255a3"/><path d="M2 10h16M10 2c-3 3-3 13 0 16M10 2c3 3 3 13 0 16" fill="none" stroke="#1e1e1f" stroke-width="1.2"/></svg>
      </li>
    </ul>
  </div>
</body>
</html>
```